OBK Farcoast Logistics Limited

We need the buissnes card to be very exclusive. As we are all young in our company. We need this to be the gate to make our clients feel deep interest for us.

We are focused in as International Trade advisors, and our products go from Oil Tanker Ships to Rubber balls for dogs.

Our Slogan is Making Global Local.
And our main marketing will be through Internet.

We were stablished in 2009 In Mexico and we also have offices in Hong Kong.
We have representatives in China and Europe.

Target Market(s)

Is every company or Individual that wants to develop an International Project or product development or Logistic service of Goods and people.
Some of our current projects are Ship Brokerage, Mine Brokerage, Real State and Product Pormotional development.

Industry/Entity Type

It Company

Requirements
Must have
• Our Logo and slogan, and make the card accoriding to the logo.
Nice to have
• Our Colors

```html
<!DOCTYPE html>
<html lang="en">
<head>
<meta charset="utf-8">
<title>OBK Farcoast Logistics Limited – Business Card</title>
<link rel="stylesheet" href="https://fonts.googleapis.com/css2?family=Mulish:wght@400;600;700&display=swap">
<style>
  :root {
    --canvas-bg: #e9e6e1;
    --card-bg: #121212;
    --card-edge: #1c1c1c;
    --lime: #8cc63f;
    --sky: #29a9e0;
    --ink-light: #f2f2f2;
    --halo: rgba(41, 169, 224, 0.14);
  }
  * { box-sizing: border-box; margin: 0; padding: 0; }
  html, body {
    width: 1200px; height: 720px; overflow: hidden;
    background: var(--canvas-bg);
    font-family: "Mulish", Arial, sans-serif;
  }
  .stage {
    width: 1200px; height: 720px;
    display: flex; align-items: center; justify-content: center; gap: 48px;
  }
  .card {
    position: relative;
    width: 532px; height: 304px;
    background: var(--card-bg);
    border: 1px solid var(--card-edge);
    box-shadow: 0 10px 26px rgba(0,0,0,0.22);
    overflow: hidden;
  }

  /* Brand name */
  .brand { display: flex; align-items: center; }
  .brand-dot { border-radius: 50%; background: var(--sky); flex: none; }
  .brand-name {
    color: var(--lime); font-weight: 700; letter-spacing: 0.04em; line-height: 1;
  }

  /* Contact side */
  .card--contact .brand { position: absolute; left: 40px; top: 52px; gap: 10px; }
  .card--contact .brand-dot { width: 30px; height: 30px; }
  .card--contact .brand-name { font-size: 40px; }

  .contact-list {
    position: absolute; left: 40px; top: 150px;
    list-style: none; color: var(--ink-light); font-size: 14px;
  }
  .contact-list li { display: flex; align-items: center; gap: 8px; height: 22px; }
  .contact-icon { width: 13px; height: 13px; flex: none; }
  .contact-address {
    position: absolute; left: 40px; top: 250px;
    color: var(--ink-light); font-size: 13px; white-space: nowrap;
  }

  .person {
    position: absolute; right: 44px; top: 60px;
    width: 190px; height: 150px;
    display: flex; flex-direction: column; align-items: center; justify-content: center;
  }
  .person-halo {
    position: absolute; inset: 0; margin: auto; width: 150px; height: 150px;
    border-radius: 50%; background: var(--halo);
  }
  .person-name { position: relative; color: var(--lime); font-weight: 700; font-size: 17px; }
  .person-title { position: relative; color: var(--ink-light); font-size: 12px; margin-top: 2px; }

  /* Brand side */
  .card--brand .brand {
    position: absolute; left: 0; right: 0; top: 48px;
    flex-direction: column;
  }
  .card--brand .brand-dot { width: 84px; height: 84px; margin-bottom: 14px; }
  .card--brand .brand-name { font-size: 62px; }
  .web-address {
    position: absolute; left: 0; right: 0; bottom: 30px; text-align: center;
    color: var(--ink-light); font-size: 19px; letter-spacing: 0.2em;
  }
</style>
</head>
<body>
<main class="stage">

  <section class="card card--contact" aria-label="Business card, contact side">
    <div class="brand">
      <span class="brand-dot"></span>
      <span class="brand-name">OBK</span>
    </div>

    <ul class="contact-list">
      <li>
        <svg class="contact-icon" viewBox="0 0 14 14"><circle cx="7" cy="7" r="7" fill="#8cc63f"/><path d="M4.5 3.5l1.6 1.6-.8 1c.5 1 1.3 1.8 2.3 2.3l1-.8 1.6 1.6-1 1.2C6.4 10.2 3.8 7.6 3.5 4.5z" fill="#121212"/></svg>
        <span>123-456-0789</span>
      </li>
      <li>
        <svg class="contact-icon" viewBox="0 0 14 14"><circle cx="7" cy="7" r="7" fill="#8cc63f"/><rect x="5" y="3" width="4" height="8" rx="0.8" fill="#121212"/></svg>
        <span>123-456-0789</span>
      </li>
      <li>
        <svg class="contact-icon" viewBox="0 0 14 14"><circle cx="7" cy="7" r="7" fill="#8cc63f"/><rect x="3.5" y="4.5" width="7" height="5" fill="#121212"/><path d="M3.5 4.5L7 7.3l3.5-2.8" stroke="#8cc63f" stroke-width="0.8" fill="none"/></svg>
        <span>info@farcoast.com</span>
      </li>
      <li>
        <svg class="contact-icon" viewBox="0 0 14 14"><circle cx="7" cy="7" r="7" fill="#8cc63f"/><circle cx="7" cy="7" r="3.5" fill="none" stroke="#121212" stroke-width="1"/><path d="M3.5 7h7M7 3.5v7" stroke="#121212" stroke-width="0.8"/></svg>
        <span>www.farcoast.com</span>
      </li>
    </ul>
    <p class="contact-address">Street Name, City Name, State Zip Code</p>

    <div class="person">
      <span class="person-halo"></span>
      <span class="person-name">Your Name</span>
      <span class="person-title">Title</span>
    </div>
  </section>

  <section class="card card--brand" aria-label="Business card, brand side">
    <div class="brand">
      <span class="brand-dot"></span>
      <span class="brand-name">OBK</span>
    </div>
    <p class="web-address">www.farcoast.com</p>
  </section>

</main>
</body>
</html>
```